Business Card Design

We are a commercial real estate brokerage in San Francisco, leasing office buildings downtown.
I would like a clean, elegant look. Simple but powerful .

Industry/Entity Type

Business

Contact Information for Business Card

Derek Holloway
lic# 07258143
415.555.0172
derek@velt-commercial.example
velt-commercial.example

```html
<!DOCTYPE html>
<html lang="en">
<head>
<meta charset="utf-8">
<title>VELT Commercial – Business Card</title>
<link rel="stylesheet" href="https://fonts.googleapis.com/css2?family=Source+Sans+3:wght@400;600&display=swap">
<style>
  :root {
    --page-bg: #e9e7e3;
    --card-white: #ffffff;
    --card-dark: #47484a;
    --card-dark-deep: #343537;
    --brand-blue: #6f7f9c;
    --name-blue: #9fb3d3;
    --text-grey: #5d5e61;
    --text-light: #f1f2f4;
    --skyline-light: #d9dadd;
    --skyline-mid: #9a9ca1;
    --rule-grey: #3d3e40;
  }
  * { box-sizing: border-box; margin: 0; padding: 0; }
  html, body {
    width: 1200px;
    height: 950px;
    overflow: hidden;
    background: var(--page-bg);
    font-family: "Source Sans 3", "Myriad Pro", sans-serif;
  }
  .canvas {
    width: 1200px;
    height: 950px;
    display: flex;
    flex-direction: column;
    align-items: center;
    justify-content: center;
    gap: 40px;
  }
  .card {
    width: 700px;
    height: 400px;
    position: relative;
    overflow: hidden;
    box-shadow: 0 10px 28px rgba(0, 0, 0, 0.22);
  }

  /* Front */
  .card-front {
    background: var(--card-white);
    display: flex;
    flex-direction: column;
    align-items: center;
    justify-content: center;
  }
  .brand {
    display: flex;
    align-items: center;
    gap: 18px;
    margin-top: -20px;
  }
  .brand-mark {
    width: 46px;
    height: 46px;
    background: var(--brand-blue);
  }
  .brand-name {
    font-size: 46px;
    font-weight: 600;
    color: var(--brand-blue);
    letter-spacing: 3px;
    line-height: 1;
  }
  .tagline {
    margin-top: 44px;
    font-size: 19px;
    font-weight: 400;
    color: var(--text-grey);
    text-align: center;
    line-height: 1.35;
  }

  /* Back */
  .card-back { background: var(--card-white); }
  .skyline {
    position: absolute;
    top: 0;
    right: 0;
    width: 330px;
    height: 100%;
    background: linear-gradient(160deg, var(--skyline-light) 0%, var(--skyline-mid) 55%, var(--skyline-light) 100%);
  }
  .contact-panel {
    position: absolute;
    top: 0;
    left: 0;
    width: 400px;
    height: 100%;
    background: linear-gradient(120deg, var(--card-dark-deep) 0%, var(--card-dark) 55%, #6a6b6e 78%, var(--card-dark) 100%);
    padding: 110px 0 0 70px;
  }
  .panel-edge {
    position: absolute;
    top: 0;
    left: 396px;
    width: 8px;
    height: 100%;
    background: var(--rule-grey);
  }
  .contact-name {
    font-size: 30px;
    font-weight: 400;
    color: var(--name-blue);
    letter-spacing: 2px;
    text-transform: uppercase;
  }
  .contact-lines {
    list-style: none;
    margin-top: 28px;
    font-size: 20px;
    color: var(--text-light);
    line-height: 1.45;
  }
</style>
</head>
<body>
<main class="canvas">
  <section class="card card-front">
    <div class="brand">
      <span class="brand-mark" aria-hidden="true"></span>
      <span class="brand-name">VELT COMMERCIAL</span>
    </div>
    <p class="tagline">commercial real estate brokerage in San Francisco<br>leasing office buildings downtown.</p>
  </section>

  <section class="card card-back">
    <div class="skyline" role="img" aria-label="Illustration of a downtown San Francisco office tower skyline in greys"></div>
    <div class="panel-edge" aria-hidden="true"></div>
    <div class="contact-panel">
      <h1 class="contact-name">Derek Holloway</h1>
      <ul class="contact-lines">
        <li>lic# 07258143</li>
        <li>415.555.0172</li>
        <li>derek@velt-commercial.example</li>
        <li>velt-commercial.example</li>
      </ul>
    </div>
  </section>
</main>
</body>
</html>
```